Veranix - Solution provider in business consulting

Veranix is a swiss based company providing solutions for developing markets. The business covers various fields of business consulting, such as supply chain, product costs, quality management and manufacturing management. The Business operates in a efficient, straight and solution oriented manner.
The final design should communicate these characteristics. Asian people as well as as western people shall identify the qualities of the company at first sight.
The customer needs business cards with a simple view but an recognizable design, printed in high quality. Engraved elements such as the globe or simple words are possible.
Available colors are: (RAL)
102/102/102
51/102/102
153/204/153
255/102/51
Font: Calibri

```html
<!DOCTYPE html>
<html lang="en">
<head>
<meta charset="utf-8">
<title>Veranix business card</title>
<link href="https://fonts.googleapis.com/css2?family=Carlito:wght@400;700&display=swap" rel="stylesheet">
<style>
  :root {
    --bg: #e9e7e3;
    --card: #ffffff;
    --card-edge: #f3f3f3;
    --ink: #666666;
    --white: #ffffff;
  }
  * { margin: 0; padding: 0; box-sizing: border-box; }
  html, body {
    width: 1200px; height: 1022px; overflow: hidden;
    background: var(--bg);
    font-family: "Carlito", "Calibri", sans-serif;
  }
  .sheet {
    width: 1200px; height: 1022px;
    display: flex; align-items: center; justify-content: center; gap: 60px;
  }
  .card {
    position: relative;
    width: 525px; height: 300px;
    border-radius: 14px;
    background: linear-gradient(135deg, var(--card) 0%, var(--card-edge) 100%);
    box-shadow: 0 2px 10px rgba(0,0,0,0.12);
    overflow: hidden;
  }
  .card-front { display: flex; align-items: center; justify-content: center; }
  .wordmark {
    display: flex; align-items: center; gap: 14px;
    color: var(--ink); font-size: 64px; font-weight: 400; letter-spacing: 1px;
  }
  .wordmark-dot { width: 30px; height: 30px; border-radius: 50%; background: var(--ink); }
  .globe-area { position: absolute; left: 0; top: 0; width: 525px; height: 300px; }
  .contact {
    position: absolute; left: 30px; bottom: 22px;
    color: var(--white);
  }
  .contact-name { font-size: 24px; font-weight: 700; line-height: 1.1; }
  .contact-role { font-size: 13px; margin-bottom: 8px; }
  .contact-block { font-size: 14px; line-height: 1.35; padding-left: 26px; }
  .contact-lines { margin-top: 4px; }
  .contact-line { display: flex; align-items: center; gap: 8px; font-size: 14px; line-height: 1.4; }
  .contact-line svg { width: 13px; height: 13px; flex: none; }
</style>
</head>
<body>
<main class="sheet">
  <section class="card card-front" aria-label="Business card front">
    <div class="wordmark"><span class="wordmark-name">veranix</span><span class="wordmark-dot"></span></div>
  </section>

  <section class="card card-back" aria-label="Business card back">
    <svg class="globe-area" viewBox="0 0 525 300" role="img" aria-label="Large engraved grey globe with world map">
      <defs>
        <linearGradient id="globe-fill" x1="0" y1="0" x2="1" y2="1">
          <stop offset="0" stop-color="#8c8c8c"/>
          <stop offset="0.6" stop-color="#6e6e6e"/>
          <stop offset="1" stop-color="#5a5a5a"/>
        </linearGradient>
      </defs>
      <circle cx="160" cy="260" r="240" fill="url(#globe-fill)"/>
    </svg>
    <div class="contact">
      <div class="contact-name">Lukas Brenner</div>
      <div class="contact-role">CEO</div>
      <div class="contact-block">Veranix GmbH Mattenweg<br>14 8570 Lindenau Switzerland</div>
      <div class="contact-lines">
        <div class="contact-line">
          <svg viewBox="0 0 14 14"><rect x="3" y="1" width="8" height="12" rx="1.5" fill="none" stroke="#fff" stroke-width="1.4"/></svg>
          +41 79 555 0132
        </div>
        <div class="contact-line">
          <svg viewBox="0 0 14 14"><path d="M3 1.5 L5.5 4 L4.2 5.6 Q5.5 8.5 8.4 9.8 L10 8.5 L12.5 11 L10.8 12.6 Q5 12 1.4 3.2 Z" fill="#fff"/></svg>
          +41 71 555 0187
        </div>
        <div class="contact-line">
          <svg viewBox="0 0 14 14"><rect x="1" y="3" width="12" height="8.5" fill="none" stroke="#fff" stroke-width="1.3"/><path d="M1 3 L7 8 L13 3" fill="none" stroke="#fff" stroke-width="1.3"/></svg>
          lukas.brenner@veranix.ch
        </div>
        <div class="contact-line">
          <svg viewBox="0 0 14 14"><circle cx="7" cy="7" r="5.8" fill="none" stroke="#fff" stroke-width="1.3"/><ellipse cx="7" cy="7" rx="2.4" ry="5.8" fill="none" stroke="#fff" stroke-width="1.1"/><path d="M1.2 7 H12.8" stroke="#fff" stroke-width="1.1"/></svg>
          www.veranix.ch
        </div>
      </div>
    </div>
  </section>
</main>
</body>
</html>
```